A clean crisp business card for a Landscape Construction company. Designed to be easy to read contact/ info and also be appealing/interesting, unlike a traditional business card.

Industry/Entity Type

Landscape Construction

Contact Information for Business Card

Company name : Brambleford Landscape Construction, phone number: (877) 62Vista, website:Bramblefordyards.example, Email, sales@bramblefordyards.example

Requirements
Nice to have
• Luxurious finishes/ details…. Icons or emblems next to contact info
Should not have
• Clipart or general pictures

```html
<!DOCTYPE html>
<html lang="en">
<head>
<meta charset="utf-8">
<title>Brambleford Landscape Construction – Business Card</title>
<link rel="stylesheet" href="https://fonts.googleapis.com/css2?family=Cinzel:wght@400;600&family=Arimo:wght@400&display=swap">
<style>
  :root {
    --stage: #0e0e0f;
    --card: #2a2a2c;
    --card-deep: #242426;
    --edge: #8cc63f;
    --blue: #1f6fc5;
    --green: #8cc63f;
    --ink: #e6e6e6;
    --rule: #4a4a4d;
  }
  * { box-sizing: border-box; margin: 0; padding: 0; }
  html, body { width: 1200px; height: 820px; overflow: hidden; background: var(--stage); }
  .stage { position: relative; width: 1200px; height: 820px; }

  .card {
    position: absolute;
    width: 540px; height: 310px;
    top: 255px;
    background: linear-gradient(160deg, var(--card) 0%, var(--card-deep) 100%);
    border-left: 3px solid var(--edge);
    border-bottom: 3px solid var(--edge);
    border-radius: 2px;
  }
  .card--front { left: 45px; }
  .card--back { left: 615px; }

  .wordmark {
    position: absolute;
    font-family: "Cinzel", serif;
    font-weight: 600;
    color: var(--blue);
    text-align: right;
    line-height: 1.15;
  }
  .card--front .wordmark { right: 28px; top: 52px; font-size: 27px; }
  .card--back .wordmark { right: 30px; top: 34px; font-size: 24px; }
  .wordmark .wordmark__line { display: block; }
  .wordmark .wordmark__small { font-size: 0.52em; letter-spacing: 0.2em; }

  .mark-dot {
    position: absolute; width: 14px; height: 14px; border-radius: 50%;
    background: var(--green);
  }
  .card--front .mark-dot { right: 28px; top: 30px; }

  .divider {
    position: absolute; left: 180px; right: 28px; top: 150px;
    height: 1px; background: var(--rule);
  }

  .person { position: absolute; left: 30px; top: 160px; }
  .person__name {
    font-family: "Cinzel", serif; font-weight: 600; font-size: 22px;
    color: var(--blue); letter-spacing: 0.02em;
  }
  .person__title {
    font-family: "Arimo", sans-serif; font-size: 12px; color: var(--green);
    letter-spacing: 0.04em; margin-top: 2px;
  }

  .contacts { position: absolute; left: 30px; bottom: 24px; list-style: none; }
  .contacts li {
    display: flex; align-items: center; gap: 8px;
    font-family: "Arimo", sans-serif; font-size: 13.5px; color: var(--ink);
    line-height: 22px;
  }
  .contacts svg { width: 14px; height: 14px; fill: none; stroke: var(--blue); stroke-width: 1.6; }
  .contacts .accent { color: var(--blue); }

  .address {
    position: absolute; right: 28px; bottom: 34px;
    font-family: "Arimo", sans-serif; font-size: 13px; color: var(--ink);
    text-align: right; line-height: 18px;
  }
</style>
</head>
<body>
<main class="stage">

  <section class="card card--front" aria-label="Business card front">
    <span class="mark-dot" aria-hidden="true"></span>
    <h1 class="wordmark">
      <span class="wordmark__line">Brambleford</span>
      <span class="wordmark__line wordmark__small">Landscape Construction</span>
    </h1>
    <div class="divider" aria-hidden="true"></div>

    <div class="person">
      <p class="person__name">Elliot Marsh</p>
      <p class="person__title">MANAGING DIRECTOR</p>
    </div>

    <ul class="contacts">
      <li>
        <svg viewBox="0 0 16 16" aria-hidden="true"><path d="M4 2l2.5 3-1.5 1.5c.8 1.8 2.2 3.2 4 4L10.5 9 13.5 11.5 12 14C6.5 13.5 2.5 9.5 2 4z"/></svg>
        (877) 62Vista
      </li>
      <li>
        <svg viewBox="0 0 16 16" aria-hidden="true"><rect x="1.5" y="3.5" width="13" height="9"/><path d="M1.5 3.5L8 9l6.5-5.5"/></svg>
        sales@bramblefordyards.example
      </li>
      <li>
        <svg viewBox="0 0 16 16" aria-hidden="true"><circle cx="8" cy="8" r="6.5"/><ellipse cx="8" cy="8" rx="3" ry="6.5"/><path d="M1.5 8h13M2.5 5h11M2.5 11h11"/></svg>
        <span>www.<span class="accent">bramblefordyards</span>.example</span>
      </li>
    </ul>

    <p class="address">218 Fernhollow Road<br>Ashby Vale 40731</p>
  </section>

  <section class="card card--back" aria-label="Business card back">
    <h2 class="wordmark">
      <span class="wordmark__line">Brambleford</span>
      <span class="wordmark__line wordmark__small">Landscape Construction</span>
    </h2>
  </section>

</main>
</body>
</html>
```